Velvet Pressings Techno Label Business Card

I'm looking for a very clean business card for my Velvet Pressings music label. The label focusses on techno music. The card should include:

• my name : Tomas Brandt as "Founder & CEO"
• email address: tomas@velvet-pressings.example
• web: www.velvet-pressings.example
• facebook logo + /velvetpress
• twitter logo + /velvetpress
• soundcloud logo + /velvetpressings

Feel free to include your ideas! I'm looking forward to discuss about it.

Tomas

Industry/Entity Type

Business

Contact Information for Business Card

I don't like glossy cards. Prefer matt.

Requirements
Nice to have
• Maybe on one side the complete logo, other side just the icon.
Should not have
• Flashy stuff. Must be clean and business like style.

```html
<!DOCTYPE html>
<html lang="en">
<head>
<meta charset="utf-8">
<title>Velvet Pressings – Business Card</title>
<link rel="stylesheet" href="https://fonts.googleapis.com/css2?family=Open+Sans:wght@400;600;700&display=swap">
<style>
  :root {
    --backdrop: #e6e6e6;
    --label-orange: #f26b1d;
    --card-white: #f7f7f7;
    --text-grey: #5a5a5a;
    --shadow: rgba(0, 0, 0, 0.12);
  }
  * { box-sizing: border-box; margin: 0; padding: 0; }
  html, body {
    width: 1200px;
    height: 726px;
    overflow: hidden;
    background: var(--backdrop);
    font-family: "Open Sans", sans-serif;
  }
  .canvas {
    position: relative;
    width: 1200px;
    height: 726px;
  }
  .card {
    position: absolute;
    width: 525px;
    height: 300px;
    box-shadow: 0 6px 18px var(--shadow);
  }

  /* Front: full brand side */
  .card--front {
    left: 55px;
    top: 110px;
    background: var(--label-orange);
    display: flex;
    align-items: center;
    justify-content: center;
    gap: 18px;
  }
  .brand-dot {
    width: 40px;
    height: 40px;
    border-radius: 50%;
    background: #fff;
  }
  .brand-name {
    color: #fff;
    font-weight: 700;
    font-size: 40px;
    letter-spacing: -0.5px;
  }

  /* Back: contact side */
  .card--back {
    left: 620px;
    top: 320px;
    background: var(--card-white);
    display: flex;
    align-items: center;
    padding: 0 36px;
  }
  .back-mark {
    width: 205px;
    display: flex;
    flex-direction: column;
    align-items: center;
    gap: 14px;
  }
  .back-mark__dot {
    width: 96px;
    height: 96px;
    border-radius: 50%;
    background: var(--label-orange);
  }
  .back-mark__name {
    color: var(--label-orange);
    font-weight: 700;
    font-size: 19px;
  }
  .contact {
    margin-left: 24px;
  }
  .contact__name {
    color: var(--label-orange);
    font-size: 17px;
    font-weight: 400;
    line-height: 1.2;
  }
  .contact__role {
    color: var(--text-grey);
    font-size: 10px;
    margin-bottom: 30px;
  }
  .contact__list {
    list-style: none;
    display: flex;
    flex-direction: column;
    gap: 4px;
  }
  .contact__item {
    display: flex;
    align-items: center;
    gap: 8px;
    color: var(--text-grey);
    font-size: 11.5px;
  }
  .contact__icon {
    width: 10px;
    height: 10px;
    flex: none;
  }
  .contact__square {
    width: 10px;
    height: 10px;
    flex: none;
    background: var(--label-orange);
    border-radius: 1px;
  }
</style>
</head>
<body>
<main class="canvas">
  <section class="card card--front" aria-label="Card front">
    <span class="brand-dot" aria-hidden="true"></span>
    <span class="brand-name">Velvet Pressings</span>
  </section>

  <section class="card card--back" aria-label="Card back">
    <div class="back-mark">
      <span class="back-mark__dot" aria-hidden="true"></span>
      <span class="back-mark__name">Velvet Pressings</span>
    </div>
    <div class="contact">
      <p class="contact__name">Tomas Brandt</p>
      <p class="contact__role">Founder &amp; CEO</p>
      <ul class="contact__list">
        <li class="contact__item">
          <svg class="contact__icon" viewBox="0 0 10 10" aria-hidden="true">
            <rect x="0.5" y="2" width="9" height="6.5" fill="var(--label-orange)"/>
            <path d="M0.5 2 L5 5.6 L9.5 2" fill="none" stroke="#fff" stroke-width="0.9"/>
          </svg>
          tomas@velvet-pressings.example
        </li>
        <li class="contact__item">
          <svg class="contact__icon" viewBox="0 0 10 10" aria-hidden="true">
            <circle cx="5" cy="5" r="4.5" fill="var(--label-orange)"/>
            <ellipse cx="5" cy="5" rx="1.8" ry="4.3" fill="none" stroke="#fff" stroke-width="0.7"/>
            <line x1="0.6" y1="5" x2="9.4" y2="5" stroke="#fff" stroke-width="0.7"/>
          </svg>
          www.velvet-pressings.example
        </li>
        <li class="contact__item"><span class="contact__square" aria-hidden="true"></span>/velvetpress</li>
        <li class="contact__item"><span class="contact__square" aria-hidden="true"></span>/velvetpress</li>
        <li class="contact__item"><span class="contact__square" aria-hidden="true"></span>/velvetpressings</li>
      </ul>
    </div>
  </section>
</main>
</body>
</html>
```